Classy, Elegant, Simple Business Card Design

Looking to have a classy, simple, and elegant design. Want a top notch designed business card. I really like the look of the new torvane credit card. I also like the design I attached. I am trying to reach 21-29 year old females for booking us for there wedding or event. We offer Disc Jockey Service, Photo Booth Rentals, and Uplighting .

Target Market(s)

21-28 year old females

Contact Information for Business Card

Has to have logo, website, email, and phone number

Font styles to use
Other font styles liked:
• open to font choice, modern, clean
Designer to choose
33a6d7
0791cd
0555a3
ffffff

Requirements
Must have
• Has to have logo, website, email, and phone number
Nice to have
• I really like the design of the new torvane credit card. I also included my logo and some designs I like
Should not have
• clutter or too much info

```html
<!DOCTYPE html>
<html lang="en">
<head>
<meta charset="utf-8">
<title>Brightnote Events – Business Card</title>
<link rel="stylesheet" href="https://fonts.googleapis.com/css2?family=Roboto:wght@400;500;700&display=swap">
<style>
  :root {
    --backdrop: #b9b9b9;
    --card: #f3f3f3;
    --navy: #0a2c5e;
    --blue-deep: #0555a3;
    --blue-mid: #0791cd;
    --blue-light: #33a6d7;
    --ink: #2a2a2a;
    --rule: #b5b5b5;
  }
  * { margin: 0; padding: 0; box-sizing: border-box; }
  html, body {
    width: 1200px;
    height: 576px;
    overflow: hidden;
    background: var(--backdrop);
    font-family: "Roboto", Arial, sans-serif;
  }
  .canvas { position: relative; width: 1200px; height: 576px; }
  .card {
    position: absolute;
    top: 138px;
    width: 484px;
    height: 296px;
    background: var(--card);
    border-radius: 10px;
    overflow: hidden;
  }
  .card--front { left: 82px; }
  .card--back { left: 602px; }

  .brand-name {
    position: absolute;
    font-family: "Roboto", Arial, sans-serif;
    font-weight: 500;
    color: var(--blue-deep);
    white-space: nowrap;
    display: flex;
    align-items: center;
    gap: 10px;
  }
  .brand-name__dot {
    width: 14px; height: 14px;
    border-radius: 50%;
    background: var(--blue-mid);
  }
  .card--front .brand-name {
    left: 50%; top: 122px;
    transform: translateX(-50%);
    font-size: 34px;
  }
  .card--back .brand-name {
    left: 132px; top: 122px;
    transform: translateX(-50%);
    font-size: 25px;
  }

  .sound-band {
    position: absolute;
    left: 0; right: 0; bottom: 0;
    height: 40px;
    background: linear-gradient(to top, var(--navy) 0%, var(--blue-deep) 35%, var(--blue-light) 75%, rgba(51,166,215,0) 100%);
    opacity: 0.85;
  }

  .divider {
    position: absolute;
    left: 250px; top: 64px;
    width: 0; height: 160px;
    border-left: 2px dotted var(--rule);
  }

  .contact { position: absolute; left: 290px; top: 88px; color: var(--ink); }
  .contact__name {
    font-size: 20px; font-weight: 700; color: var(--blue-deep); line-height: 24px;
  }
  .contact__title { font-size: 12px; margin-top: 2px; line-height: 14px; }
  .contact__list { list-style: none; margin-top: 20px; }
  .contact__item {
    display: flex; align-items: center; gap: 9px;
    font-size: 12.5px; line-height: 18.5px;
  }
  .contact__icon { width: 10px; height: 10px; fill: var(--blue-deep); flex: none; }
</style>
</head>
<body>
<main class="canvas">
  <section class="card card--front">
    <div class="brand-name"><span class="brand-name__dot"></span>Brightnote Events</div>
    <div class="sound-band" role="img" aria-label="Decorative sound wave equalizer bars in blue tones"></div>
  </section>

  <section class="card card--back">
    <div class="brand-name"><span class="brand-name__dot"></span>Brightnote Events</div>
    <div class="divider"></div>
    <div class="contact">
      <p class="contact__name">Mara Ellison</p>
      <p class="contact__title">Founder &amp; CEO</p>
      <ul class="contact__list">
        <li class="contact__item">
          <svg class="contact__icon" viewBox="0 0 10 10"><path d="M1 3C1 1.5 2.5 1 5 1s4 .5 4 2L7.5 4 6.8 3H3.2L2.5 4zM2.5 5h5l1 4H1.5z"/></svg>
          555 0142 0199
        </li>
        <li class="contact__item">
          <svg class="contact__icon" viewBox="0 0 10 10"><path d="M0 2h10v6H0zM1 3v.3L5 6l4-2.7V3L5 5.6z" fill-rule="evenodd"/></svg>
          mara@brightnote-events.com
        </li>
        <li class="contact__item">
          <svg class="contact__icon" viewBox="0 0 10 10"><circle cx="5" cy="5" r="4.3" fill="none" stroke="#0555a3" stroke-width="1.1"/><path d="M.7 5h8.6M5 .7v8.6" stroke="#0555a3" stroke-width="0.9"/><ellipse cx="5" cy="5" rx="2" ry="4.3" fill="none" stroke="#0555a3" stroke-width="0.9"/></svg>
          www.brightnote-events.com
        </li>
      </ul>
    </div>
    <div class="sound-band" role="img" aria-label="Decorative sound wave equalizer bars in blue tones"></div>
  </section>
</main>
</body>
</html>
```